Instagram Story & Feed Template Design

Hey there,

We are looking for someone who can design a template for us to use each week to promote our podcast on Instagram stories and Instagram feed.

The priority of this job is the graphic design elements of the Instagram Story and Instagram Feed. (These design files will then be given to an animator who will convert these into a video template in Premiere Pro).

The podcast is called The Corinna Valdestri Show which you can view here: https://podcasts.examplecast.net/au/podcast/the-corinna-valdestri-show/id5820347716

Here is an example of how we are currently doing the Instagram Feed post. This follows the classic 'meme' style of Instagram feed post. It converts well but it's ugly :)

https://www.snapgrid.example/tv/QwR7mZk2LpX/?utm_source=ig_web_copy_link

Each week in the template we would change the:

- Title of the show (see root ledger example)
- Name of guest
- Episode #
- Episode link (eg, corinnavaldestri.example/375)
- Photo of the guest (if this ends up being a part of the winning design)
- The feed preview Cover Image of the Instagram feed post

Instagram feed dimensions: 1080 x 1080 px
Instagram story dimensions: 1080 x 1920 px

Target market is 90% female, interested in health, wellness and spirituality.

This is an example of how someone else is doing something similar (root ledger): https://www.snapgrid.example/tv/VbN4tYe9HuJ/?utm_source=ig_web_copy_link

This example can be improved by always starting with a quick 5-sec highlight of the video to get their attention (see Corinna's example above), and a prominent catchy heading (for the Feed post).

We have provided brand guidelines/style guide, logo and colours as well as a screenshot of the new website design that launches in the next week, so you can see what we are aiming for visually.

Examples of some animations we liked are as follows. While this job is not about animating, but design, this may help with ideas as to what we are looking for.

- https://clipmarket.example/item/driftlyn-motion-pack-for-vertical-video/51937208
- https://clipmarket.example/item/podcast-social-pack-vertical-and-square/63014875

Overall, the design must...

- Follow brand guidelines (attached)
- Use new imagery of Corinna (attached)
- Display clearly on Instagram feeds and get people's attention
- Use The Corinna Valdestri Show logo

Thanks :)

Theo

```html
<!DOCTYPE html>
<html lang="en">
<head>
<meta charset="utf-8">
<title>The Corinna Valdestri Show – Episode 112 Story</title>
<link rel="stylesheet" href="https://fonts.googleapis.com/css2?family=Libre+Bodoni:wght@700&family=Bodoni+Moda:ital,wght@1,400&family=Montserrat:wght@400&family=Lato:wght@700;900&display=swap">
<style>
  :root {
    --charcoal: #383d40;
    --gold: #d8b95a;
    --white: #ffffff;
    --ink: #2f3437;
    --grey-text: #55595c;
    --panel-top: #f7fbfa;
    --panel-bottom: #e6f2f1;
    --photo-light: #e9e4dc;
    --photo-mid: #c99a3c;
    --photo-dark: #6b4a30;
  }
  html, body { margin: 0; padding: 0; overflow: hidden; }
  body { width: 675px; height: 1200px; background: var(--white); position: relative; }

  .header {
    position: absolute; left: 0; top: 0; width: 675px; height: 262px;
    background: var(--charcoal);
  }
  .header__brand {
    position: absolute; left: 28px; top: 74px; width: 225px;
    font-family: "Montserrat", sans-serif; font-weight: 400;
    color: var(--white); font-size: 22px; line-height: 1.3;
    letter-spacing: 3px; text-transform: uppercase; text-align: right;
  }
  .header__divider {
    position: absolute; left: 273px; top: 72px; width: 4px; height: 127px;
    background: var(--gold);
  }
  .header__title {
    position: absolute; left: 295px; top: 60px; margin: 0;
    font-family: "Libre Bodoni", serif; font-weight: 700;
    font-size: 41px; line-height: 49px; color: var(--white);
    letter-spacing: -0.5px; text-transform: uppercase; white-space: nowrap;
  }
  .header__title .accent { color: var(--gold); }

  .feature {
    position: absolute; left: 7px; top: 269px; width: 652px; height: 652px;
    border: 5px solid var(--gold);
    background: linear-gradient(180deg, var(--panel-top), var(--panel-bottom));
  }
  .feature__brand {
    position: absolute; left: 36px; top: 56px; width: 340px;
    font-family: "Montserrat", sans-serif; font-weight: 400;
    color: var(--grey-text); font-size: 34px; line-height: 1.35;
    letter-spacing: 5px; text-transform: uppercase; text-align: right;
  }
  .feature__credentials {
    position: absolute; left: 15px; top: 318px; width: 380px;
    font-family: "Bodoni Moda", serif; font-style: italic; font-weight: 400;
    color: var(--ink); font-size: 28px; line-height: 40px;
    text-align: center; text-transform: uppercase; letter-spacing: -0.5px;
  }
  .feature__credentials p { margin: 0 0 42px; }
  .feature__photo {
    position: absolute; left: 381px; top: 20px; width: 287px; height: 643px;
    background: linear-gradient(180deg, var(--photo-light) 0%, var(--photo-dark) 30%, var(--photo-mid) 60%, var(--photo-mid) 100%);
    border-radius: 120px 120px 0 0;
  }

  .listen {
    position: absolute; left: 0; top: 955px; width: 675px; margin: 0;
    font-family: "Lato", sans-serif; font-weight: 900;
    color: var(--ink); font-size: 22.5px; line-height: 27px;
    text-align: center; text-transform: uppercase; letter-spacing: -0.3px;
  }
  .platforms {
    position: absolute; left: 0; top: 1055px; width: 675px;
    display: flex; justify-content: center; gap: 34px;
  }
  .platform {
    display: flex; align-items: center; gap: 8px;
    font-family: "Lato", sans-serif; font-weight: 900;
    font-size: 26px; color: var(--ink);
  }
  .platform__dot { width: 38px; height: 38px; border-radius: 50%; background: var(--ink); }

  .episode-bar {
    position: absolute; left: 0; top: 1122px; width: 675px; height: 35px;
    background: var(--gold);
    font-family: "Lato", sans-serif; font-weight: 700;
    color: var(--white); font-size: 21px; line-height: 35px;
    letter-spacing: 2px; text-align: center;
  }
</style>
</head>
<body>
  <header class="header">
    <div class="header__brand">The Corinna Valdestri Show</div>
    <div class="header__divider"></div>
    <h1 class="header__title"><span class="accent">On the ethics</span><br>Behind dietary<br>choices</h1>
  </header>

  <section class="feature">
    <div class="feature__brand">The Corinna Valdestri Show</div>
    <div class="feature__credentials">
      <p>Multiple<br>bestselling author</p>
      <p>#1 Podcast host</p>
      <p>Keynote speaker</p>
    </div>
    <div class="feature__photo" role="img" aria-label="Photo of the host smiling, long brown hair, mustard yellow jumpsuit"></div>
  </section>

  <p class="listen">Listen to the full episode<br>with Harriet Solenne<br>on</p>

  <div class="platforms">
    <div class="platform"><span class="platform__dot"></span>Tunevault</div>
    <div class="platform"><span class="platform__dot"></span>Streamly</div>
  </div>

  <div class="episode-bar">EPISODE 112 | corinnavaldestri.example/375</div>
</body>
</html>
```